Tech business card design

We need an amazing business card design for our new business 'Pexla' a marketing tech startup based in Sydney, Australia. We provide an online marketplace for businesses to search and buy advertising media, connect with service providers and learn more about marketing. We wish to communicate 'cool tech', reliability and professionalism and design based around our logo.

Target Market(s)

Business Owners

Contact Information for Business Card

Name
Position
Email Address
Website
Phone Number

Font styles to use
Other font styles liked:
• Avenir & Avenir Next

Colors

Designer to choose colors to be used in the design.

```html
<!DOCTYPE html>
<html lang="en">
<head>
<meta charset="UTF-8">
<title>Pexla Business Card</title>
<link rel="stylesheet" href="https://fonts.googleapis.com/css2?family=Nunito+Sans:wght@400;600;700;800;900&display=swap">
<style>
  :root {
    --navy: #0c0a4a;
    --navy-deep: #07063a;
    --violet: #2a2370;
    --silver: #c9c9d1;
    --silver-light: #f1f1f4;
    --white: #ffffff;
    --stage: #e9e9ee;
  }
  * { margin: 0; padding: 0; box-sizing: border-box; }
  html, body {
    width: 1200px; height: 900px; overflow: hidden;
    background: var(--stage);
    font-family: "Nunito Sans", Arial, sans-serif;
  }
  .canvas { position: relative; width: 1200px; height: 900px; }

  .card {
    position: absolute;
    width: 600px; height: 350px;
    border-radius: 22px;
    overflow: hidden;
    box-shadow: 0 12px 30px rgba(0,0,0,.18);
  }
  .card-front { left: 150px; top: 80px; background: var(--white); }
  .card-back  {
    left: 450px; top: 470px;
    background: linear-gradient(115deg,
      var(--navy-deep) 0%, var(--navy) 22%, var(--violet) 38%,
      var(--silver) 50%, var(--violet) 62%, var(--navy) 80%, var(--navy-deep) 100%);
  }

  .front-shape { position: absolute; inset: 0; width: 100%; height: 100%; }

  .wordmark {
    position: absolute;
    font-weight: 900;
    color: var(--navy);
    letter-spacing: -2px;
    line-height: 1;
  }
  .front-wordmark { left: 44px; top: 78px; font-size: 96px; }

  .holder { position: absolute; left: 96px; top: 214px; color: var(--navy); }
  .holder-name { font-size: 19px; font-weight: 800; letter-spacing: .5px; }
  .holder-role { font-size: 14px; font-weight: 700; margin-top: 2px; }

  .contact {
    position: absolute; right: 28px; top: 58px;
    list-style: none; text-align: right;
    color: var(--white); font-size: 14px; line-height: 1.45;
  }
  .contact li { display: flex; justify-content: flex-end; align-items: center; gap: 6px; }
  .contact svg { width: 12px; height: 12px; fill: var(--white); }
  .contact .address { margin-top: 12px; display: block; line-height: 1.3; }

  .back-wordmark {
    left: 0; right: 0; top: 125px; text-align: center;
    font-size: 110px; color: rgba(200,200,225,.55);
  }
</style>
</head>
<body>
<main class="canvas">

  <section class="card card-front">
    <svg class="front-shape" viewBox="0 0 600 350" preserveAspectRatio="none" aria-hidden="true">
      <defs>
        <linearGradient id="navyField" x1="0" y1="0" x2="1" y2="1">
          <stop offset="0" stop-color="#0c0a4a"/>
          <stop offset=".55" stop-color="#2a2370"/>
          <stop offset=".75" stop-color="#9a98b2"/>
          <stop offset="1" stop-color="#0c0a4a"/>
        </linearGradient>
        <linearGradient id="silverBand" x1="0" y1="1" x2="1" y2="0">
          <stop offset="0" stop-color="#9c9ca8"/>
          <stop offset=".4" stop-color="#f1f1f4"/>
          <stop offset=".8" stop-color="#b8b8c4"/>
          <stop offset="1" stop-color="#7d7d8c"/>
        </linearGradient>
      </defs>
      <path d="M415 0 L600 0 L600 350 L0 350 L0 300 C210 300 380 200 415 0 Z" fill="url(#navyField)"/>
      <path d="M0 290 C200 292 372 196 408 0 L415 0 C380 200 210 300 0 300 Z" fill="url(#silverBand)"/>
      <path d="M0 318 C230 318 400 230 440 40 C412 215 250 306 0 306 Z" fill="url(#silverBand)" opacity=".9"/>
    </svg>

    <div class="wordmark front-wordmark">Pexla</div>

    <div class="holder">
      <div class="holder-name">JORDAN REYES</div>
      <div class="holder-role">Position</div>
    </div>

    <ul class="contact">
      <li><svg viewBox="0 0 24 24"><path d="M6.6 10.8a15 15 0 006.6 6.6l2.2-2.2a1 1 0 011-.25 11.4 11.4 0 003.6.6 1 1 0 011 1V20a1 1 0 01-1 1A17 17 0 013 4a1 1 0 011-1h3.5a1 1 0 011 1c0 1.25.2 2.45.6 3.6a1 1 0 01-.25 1z"/></svg>012-345-6789</li>
      <li><svg viewBox="0 0 24 24"><path d="M2 5h20v14H2zm2 2v.5l8 5 8-5V7zm0 3v7h16v-7l-8 5z"/></svg>info@pexla.com</li>
      <li><svg viewBox="0 0 24 24"><path d="M12 2a10 10 0 100 20 10 10 0 000-20zm0 2c.9 1.2 1.6 2.6 2 4h-4c.4-1.4 1.1-2.8 2-4zM4.3 14a8 8 0 010-4h3.4a16 16 0 000 4zm.9 2h3a14 14 0 001.3 3.5A8 8 0 015.2 16zm3-8h-3a8 8 0 014.3-3.5A14 14 0 008.2 8zM12 20c-.9-1.2-1.6-2.6-2-4h4c-.4 1.4-1.1 2.8-2 4zm2.3-6H9.7a14 14 0 010-4h4.6a14 14 0 010 4zm.2 5.5A14 14 0 0015.8 16h3a8 8 0 01-4.3 3.5zM16.3 14a16 16 0 000-4h3.4a8 8 0 010 4zm-.5-6a14 14 0 00-1.3-3.5A8 8 0 0118.8 8z"/></svg>www.pexla.com</li>
      <li class="address">Street Name, City Name<br>Zipcode:012345</li>
    </ul>
  </section>

  <section class="card card-back">
    <div class="wordmark back-wordmark">Pexla</div>
  </section>

</main>
</body>
</html>
```